Brenwick Coaching Website

I would like someone to design my website. I have an existing site which is really basic and needs an overhaul. I have attached a powerpoint with all the information I require. I am flexible with the design and layout and am ok with graphics being added to enhance the attractiveness of the site.

```html
<!DOCTYPE html>
<html lang="en">
<head>
<meta charset="utf-8">
<title>Brenwick Coaching</title>
<link rel="stylesheet" href="https://fonts.googleapis.com/css2?family=Cinzel:wght@400;700&family=Arimo:wght@400&display=swap">
<style>
:root{
  --brand-red:#9b1b2e;
  --brand-deep:#8b1a2e;
  --text-grey:#555555;
  --panel:#efefef;
  --panel-line:#d3d3d3;
  --white:#ffffff;
  --menu-top:#f7f7f7;
  --menu-bottom:#dcdcdc;
  --logo-blue:#2b6cb5;
}
*{margin:0;padding:0;box-sizing:border-box}
html,body{width:1200px;height:775px;overflow:hidden;background:var(--white)}
body{position:relative;font-family:"Arimo",Arial,sans-serif;color:var(--text-grey)}
.site-header{position:absolute;left:0;top:0;width:1200px;height:74px;background:var(--white)}
.brand{position:absolute;left:171px;top:22px;display:flex;align-items:center;gap:8px;font-family:"Cinzel",serif;font-size:22px;font-weight:700;color:var(--logo-blue)}
.brand-mark{width:14px;height:14px;background:var(--logo-blue)}
.header-contact{position:absolute;left:816px;top:18px;font-size:11px;line-height:23px;color:var(--brand-deep)}
.contact-line{display:flex;align-items:center;gap:6px}
.contact-line svg{width:14px;height:11px;flex:none}
.hero{position:absolute;left:0;top:74px;width:1200px;height:622px;
  background:
   radial-gradient(circle at 50% 2%,rgba(250,170,130,.95) 0,rgba(230,110,110,.6) 22%,rgba(0,0,0,0) 45%),
   radial-gradient(circle at 95% 20%,rgba(210,80,40,.7) 0,rgba(0,0,0,0) 25%),
   radial-gradient(circle at 5% 40%,rgba(170,30,170,.7) 0,rgba(0,0,0,0) 30%),
   radial-gradient(circle at 50% 92%,rgba(170,60,70,.7) 0,rgba(0,0,0,0) 40%),
   linear-gradient(90deg,#3a0d4a 0%,#9c2a85 20%,#b23a70 50%,#a02a5a 80%,#4a0a2a 100%)}
.hero-title{position:absolute;left:0;top:114px;width:1200px;text-align:center;font-family:"Cinzel",serif;font-size:31px;color:var(--white);letter-spacing:1px}
.main-card{position:absolute;left:171px;top:188px;width:858px;height:414px;background:var(--white)}
.service-menu{position:absolute;left:13px;top:13px;width:243px;list-style:none}
.service-menu li{height:62px;border:1px solid #cfcfcf;margin-top:-1px;background:linear-gradient(var(--menu-top),var(--menu-bottom));font-family:"Cinzel",serif;font-size:13.5px;color:#555;padding:23px 0 0 23px}
.service-menu li:first-child{margin-top:0}
.welcome{position:absolute;left:270px;top:13px;width:575px;height:309px;background:var(--panel);border:1px solid var(--panel-line)}
.welcome h1{position:absolute;left:26px;top:22px;font-family:"Cinzel",serif;font-weight:400;font-size:18px;line-height:26px;color:var(--brand-deep)}
.welcome h1 .big{font-size:23px}
.welcome-copy{position:absolute;left:25px;top:84px;width:320px;font-size:10.8px;line-height:20px}
.welcome-copy p+p{margin-top:19px}
.cta-lead{position:absolute;left:25px;top:215px;font-size:13px;color:var(--brand-deep)}
.welcome-contact{position:absolute;left:24px;top:236px;font-size:10.8px;line-height:23px;color:var(--brand-deep)}
.welcome-contact .plain{color:#222}
.portrait-frame{position:absolute;left:374px;top:16px;width:182px;height:194px;background:var(--white);border:1px solid #d0d0d0}
.portrait{position:absolute;left:8px;top:8px;width:164px;height:176px;background:linear-gradient(160deg,#a9b3a0,#6f6b5a 55%,#d98a7a)}
.about{position:absolute;left:366px;top:216px;width:200px;text-align:center}
.about h2{font-family:"Cinzel",serif;font-weight:400;font-size:15px;color:var(--brand-deep)}
.about p{margin-top:2px;font-size:10.8px;line-height:18px}
.cta-bar{position:absolute;left:13px;top:339px;width:832px;height:63px;background:var(--brand-red);color:var(--white);font-family:"Cinzel",serif;font-size:19px;text-align:center;line-height:63px;letter-spacing:.5px}
.site-footer{position:absolute;left:0;top:696px;width:1200px;height:79px;background:var(--white)}
.copyright{position:absolute;left:174px;top:33px;font-size:10.8px}
.social{position:absolute;left:842px;top:34px;display:flex;gap:22px;list-style:none}
.social li{width:12px;height:12px;border-radius:50%}
</style>
</head>
<body>
<header class="site-header">
  <div class="brand"><span class="brand-mark"></span>Brenwick Coaching</div>
  <div class="header-contact">
    <div class="contact-line"><svg viewBox="0 0 14 11"><rect x="0" y="0" width="14" height="11" fill="#8a8a8a"/><path d="M0 0 L7 6 L14 0" stroke="#fff" fill="none"/></svg>Email us : maren.doyle@brenwickcoaching.com</div>
    <div class="contact-line"><svg viewBox="0 0 14 11"><path d="M1 4 Q7 -1 13 4 L11 5 L10 3 L4 3 L3 5 Z" fill="#8a8a8a"/><rect x="3" y="5" width="8" height="6" rx="1" fill="#8a8a8a"/></svg>Call us : 1300 555 017</div>
  </div>
</header>

<section class="hero" role="img" aria-label="Soft out-of-focus lights in purple, pink and orange">
</section>
<h2 class="hero-title">Brenwick Coaching</h2>

<main class="main-card">
  <ul class="service-menu">
    <li>Individual Coaching (1)</li>
    <li>Group Work (2)</li>
    <li>Resources (3)</li>
    <li>Inspiration Booth (5)</li>
    <li>Individual Coaching (1)</li>
  </ul>

  <section class="welcome">
    <h1><span class="big">W</span>ELCOME TO<br><span class="big">B</span>RENWICK <span class="big">C</span>OACHING</h1>
    <div class="welcome-copy">
      <p>Welcome to Brenwick Coaching where we put a new perspective on the way you work, live and play.</p>
      <p>Through our programs you will learn new skills &amp; techniques to enable you to break through the barriers that have kept you from reaching your full potential up to now.</p>
    </div>
    <p class="cta-lead">If you're ready for change please</p>
    <div class="welcome-contact">
      <div class="contact-line"><svg viewBox="0 0 14 11"><rect x="0" y="0" width="14" height="11" fill="#8a8a8a"/><path d="M0 0 L7 6 L14 0" stroke="#fff" fill="none"/></svg>Email us : maren.doyle@brenwickcoaching.com <span class="plain">(or)</span></div>
      <div class="contact-line"><svg viewBox="0 0 14 11"><path d="M1 4 Q7 -1 13 4 L11 5 L10 3 L4 3 L3 5 Z" fill="#8a8a8a"/><rect x="3" y="5" width="8" height="6" rx="1" fill="#8a8a8a"/></svg>Call us : 1300 555 017 <span class="plain">today!</span></div>
    </div>
    <div class="portrait-frame"><div class="portrait" role="img" aria-label="Portrait photo of the coach, Maren"></div></div>
    <div class="about">
      <h2>About Maren</h2>
      <p>uncover many web sites still in their infancy. Various versions have evolved over the years...</p>
    </div>
  </section>

  <div class="cta-bar">Get your free 30 minute introductory coaching session... (4)</div>
</main>

<footer class="site-footer">
  <p class="copyright">Copyrights © 2014 Brenwick Coaching. All rights reserved</p>
  <ul class="social" aria-label="Social links">
    <li style="background:#3b5998"></li>
    <li style="background:#35a7e0"></li>
    <li style="background:#d94a38"></li>
    <li style="background:#c8232c"></li>
    <li style="background:#1a77b5"></li>
    <li style="background:#f28b1e"></li>
  </ul>
</footer>
</body>
</html>
```